Film poster for The Lanterns Stay Lit - a documentary

We need a poster for our documentary, The Lanterns Stay Lit, about how Ancient heroine Antigone finds new life in Beirut’s refugee camps, helping four Syrian women discover the strength to live with joy through the greatest of tragedies. The film is about 20% animated with the rest being vérité footage shot in Beirut, Lebanon. The title will be in Arabic and English.

Please check out our trailer here: https://www.fundmarrow.example/projects/417306582/the-lanterns-stay-lit?ref=qopxt3

We've included some assets from the film as well as style references of other film posters we've liked.

The designer we use will also get a credit in the film.

Target Market(s)

Documentary film festivals

Industry/Entity Type

Film Production

Font styles to use
Sans Serif

Colors

Designer to choose colors to be used in the design.

Requirements
Must have
• The Title in Both English and Arabic (Can provide the text for the arabic)
• Space at the bottom to overlay film credits
Nice to have
• Include the texture of the wall and perhaps integrate both photographic and graphic imagery
Should not have
• Shouldn't be too busy - minimalistic

```html
<!DOCTYPE html>
<html lang="en">
<head>
<meta charset="utf-8">
<title>The Lanterns Stay Lit – Film Poster</title>
<link rel="stylesheet" href="https://fonts.googleapis.com/css2?family=Passion+One:wght@400;700&family=Oswald:wght@400&family=Noto+Sans+Arabic:wght@400&display=swap">
<style>
  :root {
    --backdrop: #e9e7e3;
    --paper: #ffffff;
    --cloud-light: #fbe3b8;
    --cloud-mid: #f6c58e;
    --cloud-warm: #eea47f;
    --cloud-rose: #dc9a98;
    --glow: #fdf0a6;
    --plum: #5b1e4c;
    --ink: #1b1417;
    --figure-purple: #5a2a62;
    --figure-blue: #6fb3e0;
  }
  * { margin: 0; padding: 0; box-sizing: border-box; }
  html, body {
    width: 1200px;
    height: 1148px;
    overflow: hidden;
    background: var(--backdrop);
  }
  .poster {
    position: absolute;
    left: 195px;
    top: 24px;
    width: 810px;
    height: 1100px;
    background: var(--paper);
    box-shadow: 0 2px 10px rgba(0,0,0,0.08);
  }
  .poster__sky {
    position: absolute;
    left: 36px;
    top: 42px;
    right: 36px;
    bottom: 40px;
    border-radius: 6px;
    background:
      radial-gradient(ellipse 30% 26% at 50% 42%, var(--glow) 0%, rgba(253,240,166,0) 100%),
      radial-gradient(ellipse 60% 40% at 20% 20%, var(--cloud-rose) 0%, rgba(220,154,152,0) 70%),
      radial-gradient(ellipse 60% 45% at 85% 55%, var(--cloud-warm) 0%, rgba(238,164,127,0) 70%),
      linear-gradient(180deg, var(--cloud-mid) 0%, var(--cloud-warm) 45%, var(--cloud-light) 80%, var(--cloud-light) 100%);
  }
  .poster__title-ar {
    position: absolute;
    top: 172px;
    left: 0;
    right: 0;
    text-align: center;
    font-family: "Noto Sans Arabic", sans-serif;
    font-size: 44px;
    color: var(--ink);
    direction: rtl;
  }
  .poster__figure {
    position: absolute;
    left: 285px;
    top: 300px;
    width: 210px;
    height: 430px;
    border-radius: 90px 90px 10px 10px;
    background: linear-gradient(180deg, var(--figure-purple) 0%, var(--figure-blue) 55%, var(--figure-purple) 100%);
    opacity: 0.9;
  }
  .poster__title-en {
    position: absolute;
    left: 180px;
    top: 760px;
    font-family: "Passion One", sans-serif;
    color: var(--plum);
    line-height: 0.85;
  }
  .poster__title-small {
    display: block;
    font-size: 36px;
    letter-spacing: 1px;
    text-transform: uppercase;
  }
  .poster__title-large {
    display: block;
    font-size: 130px;
    font-weight: 700;
  }
  .poster__notes {
    position: absolute;
    left: 200px;
    right: 120px;
    top: 905px;
    text-align: center;
    font-family: "Oswald", sans-serif;
    font-size: 12px;
    line-height: 1.4;
    color: var(--ink);
  }
</style>
</head>
<body>
  <main class="poster">
    <div class="poster__sky" role="img" aria-label="Soft painted clouds in peach, rose and cream tones"></div>
    <h2 class="poster__title-ar" lang="ar">الفوانيس تبقى مضاءة</h2>
    <div class="poster__figure" role="img" aria-label="Illustration of a woman in a purple headscarf holding a child in a blue shirt"></div>
    <h1 class="poster__title-en">
      <span class="poster__title-small">The Lanterns</span>
      <span class="poster__title-large">Stay Lit</span>
    </h1>
    <p class="poster__notes">
      The Title in Both English and Arabic (Can provide the text for the arabic)<br>
      - Space at the bottom to overlay film credits&nbsp; Nice to Have:
    </p>
  </main>
</body>
</html>
```